Business Card Design

We need a business card design for a Dry cleaners in Brisbane, Australia. We are trying to promote a fresh/clean image consistent with our website. www.pinnelgarmentcare.com.au

Looking for a professional neat card that's easy to read.

Target Market(s)

Customers looking for a professional, fresh and clean drycleaners.

Industry/Entity Type

Business

Contact Information for Business Card

See our existing business card. The Fax number (07) 3468 5270 to be removed.

Requirements
Must have
• All the details on current business card less the fax number.
Nice to have
• I like white text on coloured background. Blue works well as we are located near the water...

```html
<!DOCTYPE html>
<html lang="en">
<head>
<meta charset="utf-8">
<title>Pinnel Garment Care – Business Card</title>
<link rel="stylesheet" href="https://fonts.googleapis.com/css2?family=Exo+2:wght@400;500;700&family=Oswald:wght@500&display=swap">
<style>
  :root {
    --page-bg: #e9eaee;
    --card-white: #f7f8fa;
    --brand-blue: #3a4a9c;
    --logo-blue: #2f3d8f;
    --accent-red: #e0353b;
    --strip-grey-top: #eef0f3;
    --strip-grey-bottom: #d9dce2;
    --text-white: #ffffff;
    --text-dark: #2a2d3a;
    --icon-grey: #3c3f48;
  }
  * { box-sizing: border-box; margin: 0; padding: 0; }
  html, body { width: 1200px; height: 769px; overflow: hidden; }
  body { background: var(--page-bg); font-family: "Exo 2", sans-serif; position: relative; }

  .card {
    position: absolute; left: 100px; top: 92px; width: 1000px; height: 585px;
    background: var(--card-white); box-shadow: 0 10px 30px rgba(0,0,0,.15); overflow: hidden;
  }

  .brand {
    position: absolute; top: 0; left: 0; right: 0; height: 200px;
    display: flex; align-items: center; justify-content: center; gap: 22px;
  }
  .brand-dot { width: 34px; height: 34px; border-radius: 50%; background: var(--logo-blue); }
  .brand-name { font-weight: 700; font-size: 58px; color: var(--logo-blue); letter-spacing: 1px; }

  .contact-band {
    position: absolute; left: 0; right: 0; top: 200px; height: 290px;
    background: var(--brand-blue);
    border-top: 7px solid var(--accent-red); border-bottom: 7px solid var(--accent-red);
  }
  .contact-col {
    position: absolute; top: 40px; width: 300px; margin-left: -150px;
    display: flex; flex-direction: column; align-items: center; color: var(--text-white);
    text-align: center; white-space: nowrap;
  }
  .col-person { left: 18%; }
  .col-web { left: 50%; }
  .col-phone { left: 82%; }
  .icon-disc {
    width: 86px; height: 86px; border-radius: 50%; background: #d8dbe6;
    border: 4px solid #9aa2c8; display: flex; align-items: center; justify-content: center;
    margin-bottom: 30px;
  }
  .person-name { font-family: "Oswald", sans-serif; font-weight: 500; font-size: 34px; line-height: 36px; letter-spacing: 1px; }
  .person-title { font-size: 12px; letter-spacing: 1.2px; margin-top: 4px; }
  .contact-line { font-size: 19px; line-height: 28px; letter-spacing: .3px; }
  .col-phone .contact-line { font-size: 21px; letter-spacing: 1.5px; }

  .social-strip {
    position: absolute; left: 0; right: 0; top: 490px; height: 80px;
    background: linear-gradient(to bottom, var(--strip-grey-top), var(--strip-grey-bottom));
    display: flex; align-items: center; padding-left: 90px;
  }
  .follow-label { color: var(--text-dark); }
  .follow-title { font-size: 25px; font-weight: 500; letter-spacing: 1px; line-height: 1; }
  .follow-sub { font-size: 11px; letter-spacing: 1px; margin-top: 6px; }
  .social-icons { display: flex; gap: 22px; margin-left: 54px; }
  .social-icon { width: 28px; height: 28px; background: var(--icon-grey); border-radius: 4px; }
  .card-base { position: absolute; left: 0; right: 0; top: 570px; height: 8px; background: var(--accent-red); }
</style>
</head>
<body>
  <div class="card">
    <header class="brand">
      <span class="brand-dot"></span>
      <span class="brand-name">Pinnel Garment Care</span>
    </header>

    <section class="contact-band">
      <div class="contact-col col-person">
        <div class="icon-disc">
          <svg width="44" height="44" viewBox="0 0 44 44"><circle cx="22" cy="15" r="9" fill="#3a4a9c"/><path d="M6 40 a16 14 0 0 1 32 0 z" fill="#3a4a9c"/></svg>
        </div>
        <div class="person-name">DANA WHITLOCK</div>
        <div class="person-title">GENERAL MANAGER</div>
      </div>
      <div class="contact-col col-web">
        <div class="icon-disc">
          <svg width="48" height="48" viewBox="0 0 48 48" fill="none" stroke="#3a4a9c" stroke-width="3"><circle cx="24" cy="24" r="19"/><ellipse cx="24" cy="24" rx="8" ry="19"/><line x1="5" y1="24" x2="43" y2="24"/><path d="M9 14h30M9 34h30"/></svg>
        </div>
        <div class="contact-line">dana@pinnelgarmentcare.com.au</div>
        <div class="contact-line">www.pinnelgarmentcare.com.au</div>
      </div>
      <div class="contact-col col-phone">
        <div class="icon-disc">
          <svg width="30" height="46" viewBox="0 0 30 46"><rect x="2" y="2" width="26" height="42" rx="4" fill="none" stroke="#3a4a9c" stroke-width="3"/><rect x="6" y="8" width="18" height="26" fill="#3a4a9c"/><circle cx="15" cy="39" r="2" fill="#3a4a9c"/></svg>
        </div>
        <div class="contact-line">(07) 3468 5281</div>
        <div class="contact-line">0421 558 184</div>
      </div>
    </section>

    <footer class="social-strip">
      <div class="follow-label">
        <div class="follow-title">FOLLOW US</div>
        <div class="follow-sub">ON SOCIAL NETWORKS</div>
      </div>
      <div class="social-icons">
        <span class="social-icon"></span>
        <span class="social-icon"></span>
        <span class="social-icon"></span>
        <span class="social-icon"></span>
      </div>
    </footer>
    <div class="card-base"></div>
  </div>
</body>
</html>
```